One page front and back healthcare law brochure

Our small law firm provides legal services to businesses in the health care industry. We would like a single page 8.5x11 front and back brochure that highlights the services we offer. The intent of the brochure is to communicate our professionalism, high work quality, and depth of experience in healthcare law.
Target Market(s)
Doctors, Hospitals, Medical practices, Dental practices, Healthcare clinics, Healthcare tech companies, Healthcare entrepreneurs, Nurses, Med Spas, Pain Management Clinics, Weight Loss Clinics
Industry/Entity Type
Legal, Healthcare
Requirements
Nice to have
- Visually align with https://vennory.law/ and https://vennory.law/health-care/

```html
<!DOCTYPE html>
<html lang="en">
<head>
<meta charset="utf-8">
<title>Vennory Law Healthcare Law Brochure</title>
<link href="https://fonts.googleapis.com/css2?family=Montserrat:wght@500;700;800&family=Roboto+Condensed:wght@400;700&display=swap" rel="stylesheet">
<style>
:root{
  --yellow:#f0e82c;
  --blue:#1c54a8;
  --navy:#1a4f9e;
  --sky:#6ccff0;
  --white:#ffffff;
  --ink:#1d2a44;
  --backdrop:#8c8c8c;
  --photo-a:#c9d3dd;
  --photo-b:#e9edf1;
  --photo-c:#b3a48f;
}
*{box-sizing:border-box;margin:0;padding:0}
html,body{width:772px;height:1200px;overflow:hidden;background:var(--backdrop)}
.sheet{position:absolute;left:176px;width:420px;height:590px;background:var(--yellow);overflow:hidden;font-family:"Roboto Condensed",sans-serif;color:#1a1a1a}
.sheet--front{top:6px}
.sheet--back{top:604px}
.top-shape{position:absolute;left:0;top:0;width:420px;height:260px}
.brand{position:absolute;top:24px;display:flex;align-items:center;gap:7px}
.brand__mark{width:14px;height:14px;border-radius:50%;background:var(--blue)}
.brand__name{font-family:"Montserrat",sans-serif;font-weight:700;font-size:18px;color:var(--blue);letter-spacing:-.2px;line-height:1}
.sheet--front .brand{right:18px}
.sheet--back .brand{left:18px}
.photo{position:absolute;left:17px;top:72px;width:386px;height:170px;border-radius:4px}
.photo--desk{background:linear-gradient(135deg,var(--photo-a),var(--photo-b) 55%,#2f6cb6)}
.photo--meeting{background:linear-gradient(120deg,var(--photo-c),#d9e3ee 50%,#1f4a86)}
.intro{position:absolute;left:20px;right:20px;top:252px;text-align:center}
.intro h2{font-family:"Montserrat",sans-serif;font-weight:800;font-size:9.6px;color:var(--blue);margin-bottom:3px}
.intro p{font-size:6.4px;line-height:1.5}
.panel{position:absolute;left:0;width:420px;background:var(--blue);border-radius:0 16px 0 0;color:var(--white)}
.sheet--front .panel{top:320px;height:236px;padding:16px 18px 0}
.sheet--back .panel{top:434px;height:122px;padding:12px 18px 0}
.panel h3{font-family:"Montserrat",sans-serif;font-weight:800;font-size:9.6px;color:var(--yellow);margin-bottom:2px}
.sheet--back .panel h3{font-size:11px;margin-bottom:6px}
.panel p{font-size:6.4px;line-height:1.5}
.cols{display:flex;gap:14px;margin-top:8px}
.cols p{flex:1}
.cols .col-right{padding-top:12px;border-left:0.5px solid rgba(255,255,255,.5);padding-left:12px}
.closing{text-align:center;margin-top:10px}
.reasons{list-style:none}
.reasons li{font-size:6.4px;line-height:1.45;padding-left:8px;position:relative;margin-bottom:3px}
.reasons li::before{content:"";position:absolute;left:0;top:3px;width:3.5px;height:3.5px;border-radius:50%;background:var(--yellow)}
.reasons b{font-weight:700}
.footer{position:absolute;left:0;bottom:0;width:420px;height:48px}
.footer__bg{position:absolute;left:0;top:0}
.contact{position:absolute;left:29px;top:9px;font-family:"Montserrat",sans-serif;color:var(--navy)}
.contact__label{font-size:8px;font-weight:500}
.contact__phone{font-size:15.5px;font-weight:800;display:flex;align-items:center;gap:4px;margin-top:1px}
.contact__icon{flex:none}
.address{position:absolute;right:22px;top:14px;width:190px;text-align:center;font-family:"Montserrat",sans-serif;font-size:5.6px;font-weight:500;color:var(--ink);line-height:2.2}
.address__icon{vertical-align:-1px;margin-right:2px}
.services{position:absolute;left:17px;top:256px;width:390px;height:170px}
.service{position:absolute;display:flex;gap:7px}
.service__icon{flex:none;width:22px;height:22px;border-radius:50%;background:var(--blue);border:1.5px solid var(--white);box-shadow:0 0 0 1px var(--blue)}
.service h4{font-family:"Montserrat",sans-serif;font-weight:800;font-size:9.2px;color:var(--blue);line-height:1.05;margin-bottom:1px}
.service p{font-size:6.2px;line-height:1.45}
.rail{position:absolute;width:0.6px;background:var(--blue)}
</style>
</head>
<body>

<section class="sheet sheet--front">
  <svg class="top-shape" viewBox="0 0 420 260" aria-hidden="true">
    <rect width="420" height="260" fill="var(--yellow)"/>
    <path d="M0 0 H420 V240 H403 V150 C330 150 300 75 230 70 C170 66 140 60 120 46 C90 20 60 25 40 35 C20 45 8 70 8 90 V240 H0 Z" fill="var(--white)"/>
    <path d="M0 0 H165 C145 8 130 18 120 30 C95 18 55 18 30 32 C15 40 5 50 0 60 Z" fill="var(--yellow)"/>
  </svg>
  <div class="brand">
    <span class="brand__mark"></span>
    <span class="brand__name">VENNORY LAW</span>
  </div>
  <div class="photo photo--desk" role="img" aria-label="Photo of a clinician writing on a clipboard beside a laptop and stethoscope"></div>
  <div class="intro">
    <h2>YOUR TRUSTED PARTNER IN HEALTHCARE LAW</h2>
    <p>At VENNORY.LAW, our dedicated Healthcare Law Practice Group is committed to safeguarding the interests of healthcare businesses like yours. Our team understands the unique challenges of this highly regulated industry. We are experienced in navigating the complexities of healthcare law to protect your business, allowing you to focus on what you do best: delivering exceptional care.</p>
  </div>
  <div class="panel">
    <h3>PROTECTING &amp; HELPING YOUR BUSINESS GROW</h3>
    <p>Whether you're starting a new business or managing an established enterprise, the focus of your attention and energy is on developing and commercializing your practice, products, and/or services. Due to time constraints and the overwhelming amount of work your business requires, proper legal planning sometimes takes a back seat. We can help. VENNORY.LAW seeks to relieve the stress and anxiety associated with unaddressed legal issues by handling these challenges and allowing our clients to focus on growing their companies.</p>
    <div class="cols">
      <p>Our Healthcare Law practice encompasses a wide range of services. We guide clients through the proper establishment of new businesses, and the myriad issues that arise as companies interact with the public, other companies, regulatory bodies, and the government. We help make sure businesses are correctly organized and comply with state and federal laws, rules, and regulations pertaining to raising capital, acquiring other businesses or assets, protecting patient information, complying with health law regulations and statutes, and adding and removing owners.</p>
      <p class="col-right">Buying a healthcare business, cementing a strategic partnership, and executing an exit event are all fraught with pitfalls and unexpected risks. When a deal or contract needs to get negotiated, documented, and closed - we excel. We fight to get the right deal terms for our clients and offer creative solutions to help navigate these minefields and achieve a successful result.</p>
    </div>
    <p class="closing">We work with all forms of businesses including partnerships, limited liability companies (LLCs), and corporations.<br>Regardless of the type of business, it is imperative that the potential legal threats and obstacles the<br>business may face are properly addressed.</p>
  </div>
  <div class="footer">
    <svg class="footer__bg" width="420" height="48" viewBox="0 0 420 48" aria-hidden="true">
      <rect width="420" height="48" fill="var(--sky)"/>
      <path d="M0 0 H190 C205 0 210 10 212 22 V48 H0 Z" fill="var(--yellow)"/>
    </svg>
    <div class="contact">
      <div class="contact__label">Contact Us Today:</div>
      <div class="contact__phone"><svg class="contact__icon" width="10" height="12" viewBox="0 0 10 12" aria-hidden="true"><path d="M2 1 L4 1 L5 4 L3.5 5 C4 7 5 8.5 6.5 9 L7.5 7.5 L9.5 9 L9 11 C5 11 1 6 1 2 Z" fill="none" stroke="var(--navy)" stroke-width="1"/></svg>(555) 214-0190</div>
    </div>
    <div class="address">
      <div><svg class="address__icon" width="6" height="7" viewBox="0 0 6 7" aria-hidden="true"><path d="M3 6.5 C1 4 0.5 3 0.5 2.5 A2.5 2.5 0 0 1 5.5 2.5 C5.5 3 5 4 3 6.5 Z" fill="none" stroke="var(--ink)" stroke-width=".7"/></svg>418 Marlow Avenue, Suite 120 Eastbrook, NC, 28000</div>
      <div><svg class="address__icon" width="7" height="5" viewBox="0 0 7 5" aria-hidden="true"><rect x=".4" y=".4" width="6.2" height="4.2" fill="none" stroke="var(--ink)" stroke-width=".7"/><path d="M.4 .4 L3.5 2.8 L6.6 .4" fill="none" stroke="var(--ink)" stroke-width=".7"/></svg>info@vennory.law</div>
    </div>
  </div>
</section>

<section class="sheet sheet--back">
  <svg class="top-shape" viewBox="0 0 420 260" aria-hidden="true">
    <rect width="420" height="260" fill="var(--yellow)"/>
    <path d="M0 0 H420 V60 C410 40 395 28 375 22 C345 14 315 25 300 45 C270 62 230 66 190 70 C120 76 90 150 17 150 V240 H0 Z" fill="var(--white)"/>
    <path d="M420 0 H255 C275 8 290 22 300 45 C320 22 350 14 375 22 C395 28 410 40 420 60 Z" fill="var(--yellow)"/>
  </svg>
  <div class="brand">
    <span class="brand__mark"></span>
    <span class="brand__name">VENNORY LAW</span>
  </div>
  <div class="photo photo--meeting" role="img" aria-label="Photo of two doctors meeting with a business client at a table"></div>
  <div class="services">
    <div class="rail" style="left:11px;top:26px;height:120px"></div>
    <div class="rail" style="left:215px;top:26px;height:50px"></div>
    <div class="service" style="left:0;top:2px;width:190px">
      <span class="service__icon"></span>
      <div><h4>Medical Practices</h4><p>Navigating the intricate landscape of healthcare regulations, regulatory compliance, and business legal issues. We ensure that your practice operates smoothly while avoiding costly legal pitfalls.</p></div>
    </div>
    <div class="service" style="left:204px;top:0;width:186px">
      <span class="service__icon"></span>
      <div><h4>Med Spas</h4><p>Guiding med spas through confusing and ever-changing regulations, licensing, and compliance issues while ensuring their operations are legally sound.</p></div>
    </div>
    <div class="service" style="left:0;top:72px;width:200px">
      <span class="service__icon"></span>
      <div><h4>Medical Device Companies</h4><p>Providing counsel on regulatory compliance, intellectual property, product liability, and contracts to help device manufacturers succeed in a competitive marketplace.</p></div>
    </div>
    <div class="service" style="left:204px;top:62px;width:186px">
      <span class="service__icon"></span>
      <div><h4>Medical Software<br>Companies</h4><p>Addressing the unique legal needs of software companies in healthcare, including data privacy, cybersecurity, and regulatory compliance.</p></div>
    </div>
    <div class="service" style="left:0;top:133px;width:390px">
      <span class="service__icon"></span>
      <div><h4>Weight Loss and Pain Management Clinics</h4><p>Offering guidance and support on compliance, licensing, and patient care and safety to ensure exceptional care while adhering to strict regulatory standards.</p></div>
    </div>
  </div>
  <div class="panel">
    <h3>Why Choose VENNORY.LAW?</h3>
    <ul class="reasons">
      <li><b>Industry-Focused:</b> Our deep understanding of the healthcare sector enables us to provide tailored legal solutions.</li>
      <li><b>Experienced Team:</b> Our HIPAA certified attorneys have extensive experience in healthcare law, delivering effective counsel and representation.</li>
      <li><b>Proactive Approach:</b> We anticipate challenges before they arise, providing strategic advice to safeguard your business.</li>
      <li><b>Comprehensive Services:</b> From compliance to drafting legal documents to dispute resolution, we offer end-to-end legal support for most healthcare law needs.</li>
    </ul>
  </div>
  <div class="footer">
    <svg class="footer__bg" width="420" height="48" viewBox="0 0 420 48" aria-hidden="true">
      <rect width="420" height="48" fill="var(--sky)"/>
      <path d="M0 0 H190 C205 0 210 10 212 22 V48 H0 Z" fill="var(--yellow)"/>
    </svg>
    <div class="contact">
      <div class="contact__label">Contact Us Today:</div>
      <div class="contact__phone"><svg class="contact__icon" width="10" height="12" viewBox="0 0 10 12" aria-hidden="true"><path d="M2 1 L4 1 L5 4 L3.5 5 C4 7 5 8.5 6.5 9 L7.5 7.5 L9.5 9 L9 11 C5 11 1 6 1 2 Z" fill="none" stroke="var(--navy)" stroke-width="1"/></svg>(555) 214-0190</div>
    </div>
    <div class="address">
      <div><svg class="address__icon" width="6" height="7" viewBox="0 0 6 7" aria-hidden="true"><path d="M3 6.5 C1 4 0.5 3 0.5 2.5 A2.5 2.5 0 0 1 5.5 2.5 C5.5 3 5 4 3 6.5 Z" fill="none" stroke="var(--ink)" stroke-width=".7"/></svg>418 Marlow Avenue, Suite 120 Eastbrook, NC, 28000</div>
      <div><svg class="address__icon" width="7" height="5" viewBox="0 0 7 5" aria-hidden="true"><rect x=".4" y=".4" width="6.2" height="4.2" fill="none" stroke="var(--ink)" stroke-width=".7"/><path d="M.4 .4 L3.5 2.8 L6.6 .4" fill="none" stroke="var(--ink)" stroke-width=".7"/></svg>info@vennory.law</div>
    </div>
  </div>
</section>

</body>
</html>
```